The Marrowby Hotel Flyer

it is for a Pub that has been in the area for a long time but now we have changed the name and taken over as new owners and now have to try to get all the locals back, eating and drinking..

This Flyer is to try get all the locals to come try the new Marrowby Hotel.

We have a great new menu with daily food deals
Craft beers
Week nights Live music
Tuesday Comedy night
Sunday live music

Industry/Entity Type

Hotel

```html
<!DOCTYPE html>
<html lang="en">
<head>
<meta charset="utf-8">
<title>The Marrowby Hotel Flyer</title>
<link rel="stylesheet" href="https://fonts.googleapis.com/css2?family=Arimo:wght@700&family=Archivo+Black&family=Roboto+Condensed:wght@400;700&display=swap">
<style>
  :root {
    --navy: #1f2370;
    --ribbon: #3b3d98;
    --ribbon-dark: #23256a;
    --glass-light: #fbfbfb;
    --glass-mid: #e9eaea;
    --white: #ffffff;
  }
  html, body { margin: 0; padding: 0; overflow: hidden; }
  .flyer {
    position: relative;
    width: 848px;
    height: 1200px;
    overflow: hidden;
    background: var(--white);
    color: var(--navy);
    font-family: "Arimo", Arial, sans-serif;
    font-weight: 700;
  }
  .glass-backdrop {
    position: absolute;
    inset: 0;
    background:
      radial-gradient(ellipse 60% 55% at 50% 45%, var(--glass-light), transparent 70%),
      linear-gradient(90deg, var(--glass-mid) 0%, var(--glass-light) 12%, var(--white) 50%, var(--glass-light) 88%, var(--glass-mid) 100%);
  }
  .line {
    position: absolute;
    left: 0;
    width: 100%;
    text-align: center;
    margin: 0;
    line-height: 1;
    white-space: nowrap;
  }
  .brand-the { top: 82px; font-size: 40px; letter-spacing: 2px; }
  .brand-name { top: 140px; font-size: 118px; letter-spacing: 2px; }
  .brand-hotel { top: 280px; font-size: 36px; letter-spacing: 3px; }
  .address { top: 342px; font-size: 22px; }
  .invite-small { font-size: 28px; }
  .invite-big { font-size: 44px; letter-spacing: 1px; }
  .invite-1 { top: 421px; }
  .invite-2 { top: 466px; }
  .invite-3 { top: 536px; }
  .invite-4 { top: 580px; }
  .rules { position: absolute; left: 0; top: 0; }
  .deal {
    position: absolute;
    top: 684px;
    width: 260px;
    margin: 0;
    text-align: center;
    font-family: "Archivo Black", "Arial Black", sans-serif;
    font-weight: 400;
    font-size: 41px;
    line-height: 43px;
  }
  .deal-uni { left: 170px; }
  .deal-daily { left: 430px; }
  .schedule {
    font-family: "Roboto Condensed", "Arial Narrow", sans-serif;
    font-weight: 400;
  }
  .schedule-live { top: 852px; font-size: 28px; }
  .schedule-tuesday { top: 1007px; font-size: 25px; }
  .ribbons { position: absolute; left: 0; top: 0; }
  .ribbon-text {
    position: absolute;
    margin: 0;
    line-height: 1;
    color: var(--white);
    font-family: "Roboto Condensed", "Arial Narrow", sans-serif;
    font-weight: 700;
    font-size: 76px;
    white-space: nowrap;
    text-align: center;
  }
  .ribbon-live { left: 120px; top: 905px; width: 620px; }
  .ribbon-comedy { left: 140px; top: 1058px; width: 640px; }
</style>
</head>
<body>
<main class="flyer">
  <div class="glass-backdrop" role="img" aria-label="Pint glass filling the background"></div>

  <svg class="rules" width="848" height="1200" aria-hidden="true">
    <g stroke="#1f2370" stroke-width="3">
      <line x1="115" y1="382" x2="735" y2="382"/>
      <line x1="115" y1="396" x2="735" y2="396"/>
      <line x1="113" y1="648" x2="733" y2="648"/>
      <line x1="113" y1="662" x2="733" y2="662"/>
      <line x1="125" y1="826" x2="718" y2="826"/>
      <line x1="125" y1="840" x2="718" y2="840"/>
    </g>
  </svg>

  <header class="brand">
    <p class="line brand-the">THE</p>
    <h1 class="line brand-name">MARROWBY</h1>
    <p class="line brand-hotel">HOTEL</p>
  </header>

  <p class="line address">42/48 Halloway St Cnr of Fenwick st</p>

  <p class="line invite-small invite-1">Come try our</p>
  <p class="line invite-big invite-2">Great New Menu</p>
  <p class="line invite-small invite-3">and</p>
  <p class="line invite-big invite-4">Craft Beers</p>

  <p class="deal deal-uni">Uni<br>Food<br>Deals</p>
  <p class="deal deal-daily">Daily<br>Food<br>Deals</p>

  <p class="line schedule schedule-live">Week Nights + Sunday</p>

  <svg class="ribbons" width="848" height="1200" aria-hidden="true">
    <defs>
      <linearGradient id="ribbonFill" x1="0" y1="0" x2="1" y2="0">
        <stop offset="0" stop-color="#23256a"/>
        <stop offset="0.3" stop-color="#3b3d98"/>
        <stop offset="0.75" stop-color="#4d50ab"/>
        <stop offset="1" stop-color="#23256a"/>
      </linearGradient>
    </defs>
    <!-- Live music ribbon, pointing right -->
    <path d="M100 960 L100 1008 L82 1008 C60 1000 45 985 40 965 Z" fill="#23256a"/>
    <path d="M35 910 C60 898 90 898 110 905 L640 898 L745 945 L640 995 L110 992 C80 985 50 975 35 965 Z" fill="url(#ribbonFill)"/>
    <!-- Comedy night ribbon, pointing left -->
    <path d="M760 1010 C790 1012 812 1018 820 1030 L820 1060 L760 1060 Z" fill="#23256a"/>
    <path d="M210 1048 L790 1042 C805 1045 815 1050 820 1060 L820 1128 C800 1140 780 1145 760 1145 L210 1145 L105 1096 Z" fill="url(#ribbonFill)"/>
  </svg>

  <p class="ribbon-text ribbon-live">Live Music</p>
  <p class="line schedule schedule-tuesday">Tuesday</p>
  <p class="ribbon-text ribbon-comedy">Comedy Night</p>
</main>
</body>
</html>
```